Talbrook Answering Service Brochure

Design a brochure for an answering service/call center based on the information submitted/attached. Photos and text will be included. Would like it designed to complement the logo provided. This brochure will explain to the potential customer who we are and what we have to offer.

The Talbrook representatives take and processes inbound calls, 24-7-365

Target Market(s)

Any business, however, primarily Medical, oil and gas, non profits, and the service industry

Industry/Entity Type

Telecommunications

Font styles to use
Serif
Other font styles liked:
• coordinate with logo

Requirements
Must have
• Modern, bright, bold and neatly structured brochure that will complement the logo and our brand.

```html
<!DOCTYPE html>
<html lang="en">
<head>
<meta charset="utf-8">
<title>Talbrook Answering Service Brochure</title>
<link href="https://fonts.googleapis.com/css2?family=Montserrat:wght@600;700&family=Questrial&display=swap" rel="stylesheet">
<style>
:root{
  --stage:#b3b3b3;
  --charcoal:#3b3b3d;
  --charcoal-deep:#2e2e30;
  --red:#d3111b;
  --red-dark:#a50c14;
  --white:#ffffff;
  --ink:#333338;
  --photo-light:#e9ecef;
  --photo-mid:#c9cdd2;
}
*{box-sizing:border-box;margin:0;padding:0}
html,body{width:900px;height:1200px;overflow:hidden}
body{background:var(--stage);font-family:"Questrial",sans-serif;color:var(--white);position:relative}
.spread{position:absolute;left:130px;width:640px;height:460px;overflow:hidden;box-shadow:0 6px 14px rgba(0,0,0,.25)}
.spread--cover{top:80px}
.spread--inside{top:630px;background:var(--charcoal)}
.spread-art{position:absolute;inset:0}
.layer{position:absolute}
.photo{position:absolute}
.contact-block{left:40px;top:235px;width:240px;text-align:center}
.contact-title{font-family:"Montserrat",sans-serif;font-weight:700;font-size:13px;border-bottom:1px solid #888;padding-bottom:3px;margin:0 45px 6px}
.phone-line{font-size:8px;line-height:13px;display:flex;align-items:center;justify-content:center;gap:4px}
.phone-icon{width:7px;height:7px}
.web-pill{display:inline-block;background:var(--red);color:var(--white);font-size:9px;padding:2px 8px;border-radius:3px;margin:6px 0 5px}
.tagline{font-size:7.5px}
.footer-url{position:absolute;bottom:2px;font-family:"Montserrat",sans-serif;font-size:7.5px;font-weight:600;color:var(--white);width:320px;text-align:center}
.footer-url--left{left:0}.footer-url--right{left:320px}
.brand{left:340px;top:292px;display:flex;align-items:center;gap:5px}
.brand-dot{width:14px;height:14px;border-radius:50%;background:var(--red)}
.brand-name{font-family:"Montserrat",sans-serif;font-weight:700;font-size:13px;color:var(--ink);letter-spacing:.5px}
.brand-sub{left:359px;top:309px;font-size:5.5px;color:var(--ink);letter-spacing:1px}
.cover-intro{left:340px;top:350px;width:292px;font-size:8.3px;line-height:11px;color:var(--ink)}
.cover-contact{left:340px;top:400px;width:160px;color:var(--ink)}
.cover-motto{color:var(--red);font-size:8.5px;border-bottom:1px solid var(--red);padding-bottom:2px;margin-bottom:3px}
.cover-contact .phone-line{justify-content:flex-start;font-size:8px;line-height:12px}
/* inside */
.copy{font-size:5.7px;line-height:7.3px;color:#e6e6e6;text-align:justify}
.copy p{margin-bottom:4px}
.label{display:inline-block;background:var(--red);color:var(--white);font-size:8px;padding:1px 6px 1px 4px;margin-bottom:4px;border-radius:0 3px 3px 0}
.label--wide{font-size:7.8px;line-height:9px}
.ticks{list-style:none;margin-bottom:4px}
.ticks li{position:relative;padding-left:8px;font-size:5.7px;line-height:7.3px;color:#e6e6e6}
.ticks li::before{content:"";position:absolute;left:1px;top:1.5px;width:2.5px;height:4px;border:solid #e6e6e6;border-width:0 1px 1px 0;transform:rotate(40deg)}
.subhead{font-family:"Montserrat",sans-serif;font-weight:700;font-size:7px;color:var(--white);margin:2px 0 2px}
.col-about{left:8px;top:205px;width:140px}
.col-live{left:162px;top:172px;width:146px}
.col-auto{left:328px;top:12px;width:144px}
.col-special{left:480px;top:12px;width:150px}
.info-block{left:8px;top:418px;width:140px;text-align:center}
.info-title{font-size:10px;margin-bottom:2px}
.info-pill{display:inline-block;background:var(--red);font-family:"Montserrat",sans-serif;font-weight:700;font-size:8px;padding:1px 8px;border-radius:3px}
</style>
</head>
<body>

<section class="spread spread--cover" aria-label="Brochure cover spread">
  <svg class="spread-art" width="640" height="460" viewBox="0 0 640 460">
    <rect width="320" height="460" fill="#3b3b3d"/>
    <path d="M0 460 Q160 300 320 330 L320 460Z" fill="#333335"/>
    <rect x="320" width="320" height="460" fill="#ffffff"/>
    <path d="M150 0 C230 120 270 250 325 300 C420 320 540 300 640 265 L640 0Z" fill="#e4e7ea"/>
    <path d="M325 300 C420 320 540 300 640 265 L640 288 C540 320 420 332 325 312Z" fill="#d3111b"/>
    <path d="M325 312 C420 332 540 320 640 288 L640 302 C540 330 420 340 325 322Z" fill="#2e2e30"/>
    <rect y="445" width="640" height="15" fill="#d3111b"/>
  </svg>
  <div class="photo" role="img" aria-label="Photo of a smiling call center agent wearing a headset with colleagues blurred behind"
       style="left:150px;top:0;width:490px;height:300px;clip-path:path('M0 0 C80 120 120 250 175 300 C270 320 390 300 490 265 L490 0Z');background:linear-gradient(110deg,#f3f4f6 0%,#d8dbdf 45%,#c6b3a6 70%,#f1f2f4 100%)"></div>

  <div class="layer contact-block">
    <div class="contact-title">Contact Us:</div>
    <div class="phone-line"><svg class="phone-icon" viewBox="0 0 10 10"><rect width="10" height="10" rx="2" fill="#fff"/><path d="M3 2 L4.5 3.5 L3.8 4.4 Q4.8 6 5.8 6.4 L6.6 5.6 L8 7 L7 8 Q4 7.8 2 3Z" fill="#3b3b3d"/></svg>(866) 555-0142</div>
    <div class="phone-line"><svg class="phone-icon" viewBox="0 0 10 10"><rect width="10" height="10" rx="2" fill="#fff"/><path d="M3 2 L4.5 3.5 L3.8 4.4 Q4.8 6 5.8 6.4 L6.6 5.6 L8 7 L7 8 Q4 7.8 2 3Z" fill="#3b3b3d"/></svg>(409) 555-0187</div>
    <div class="web-pill">www. Talbrooksvc.com</div>
    <div class="tagline">to subscribe to a Great Service, and a Strong ROI!</div>
  </div>

  <div class="layer brand"><span class="brand-dot"></span><span class="brand-name">TALBROOK</span></div>
  <div class="layer brand-sub">ANSWERING SERVICE · EST. 1932</div>

  <p class="layer cover-intro">Talbrook Answering Service is your award winning, five start center, backed by critical redundancy and a solid infrastructure, for the highest availability possible.</p>

  <div class="layer cover-contact">
    <div class="cover-motto">Any Call - Any Time - Any Place</div>
    <div class="phone-line"><svg class="phone-icon" viewBox="0 0 10 10"><rect width="10" height="10" rx="2" fill="#d3111b"/><path d="M3 2 L4.5 3.5 L3.8 4.4 Q4.8 6 5.8 6.4 L6.6 5.6 L8 7 L7 8 Q4 7.8 2 3Z" fill="#fff"/></svg>(866) 555-0142</div>
    <div class="phone-line"><svg class="phone-icon" viewBox="0 0 10 10"><rect width="10" height="10" rx="2" fill="#d3111b"/><path d="M3 2 L4.5 3.5 L3.8 4.4 Q4.8 6 5.8 6.4 L6.6 5.6 L8 7 L7 8 Q4 7.8 2 3Z" fill="#fff"/></svg>(409) 555-0187</div>
  </div>

  <div class="footer-url footer-url--left">www. Talbrooksvc.com</div>
  <div class="footer-url footer-url--right">www. Talbrooksvc.com</div>
</section>

<section class="spread spread--inside" aria-label="Brochure inside spread">
  <svg class="spread-art" width="640" height="460" viewBox="0 0 640 460">
    <rect width="320" height="460" fill="#3b3b3d"/>
    <rect x="320" width="320" height="460" fill="#38383a"/>
    <path d="M0 0 L320 0 L320 110 C230 160 100 170 0 178Z" fill="#eef0f2"/>
    <path d="M0 178 C100 170 230 160 320 110 L320 124 C230 176 100 186 0 192Z" fill="#ffffff"/>
    <path d="M0 192 C100 186 230 176 320 124 L320 134 C230 186 100 196 0 202Z" fill="#d3111b"/>
    <path d="M420 460 C450 380 540 330 640 318 L640 460Z" fill="#ffffff"/>
    <path d="M412 460 C440 376 540 322 640 308 L640 318 C540 330 450 380 420 460Z" fill="#d3111b"/>
  </svg>
  <div class="photo" role="img" aria-label="Photo of a group of five smiling office professionals, some wearing headsets"
       style="left:0;top:0;width:320px;height:178px;clip-path:path('M0 0 L320 0 L320 110 C230 160 100 170 0 178Z');background:linear-gradient(180deg,#f2f3f5 0%,#d9d4cf 55%,#b8b2ad 100%)"></div>
  <div class="photo" role="img" aria-label="Photo of smiling call center agents with headsets in a row"
       style="left:430px;top:326px;width:210px;height:134px;clip-path:path('M0 134 C30 56 110 12 210 2 L210 134Z');background:linear-gradient(120deg,#f0f1f3 0%,#d6cbc2 50%,#a9a39e 100%)"></div>

  <div class="layer col-about">
    <span class="label">About Us:</span>
    <div class="copy">
      <p>Talbrook, over the past 84 years, has operated through wars, floods and hurricanes. Our long history is important as it shows Consistency, Professionalism, Experience, and a Can Do Attitude, which is hard to find in the answering service industry today.</p>
      <p>At Talbrook, you'll never be just another a number. We will become part of YOUR team on day one and remain there, ready and honored to serve by providing reliable, professional answering services, 24-7-365, as needed.</p>
    </div>
    <span class="label label--wide">Still Growing? Find a Scalable<br>Phone Answering Service</span>
    <div class="copy"><p>A scalable solution is one that doesn't waste resources when you don't need them, but easily adapts to future growth. All of our services at Talbrook grow with you, meaning you don't pay for additional support until you need it.</p></div>
  </div>
  <div class="layer info-block">
    <div class="info-title">Any information:</div>
    <span class="info-pill">www. Talbrooksvc.com</span>
  </div>

  <div class="layer col-live">
    <span class="label label--wide">Automated or Live – Answering<br>Services That Work for You</span>
    <div class="copy"><p>Tell us about your needs and your budget and we'll do the rest. Talbrook selects a system that satisfies your basic requirements, then evaluates your business to find a long-term solution that will work for you and your customers.</p></div>
    <span class="label">Live Answering Service</span>
    <div class="copy"><p>Clearline Response is more than an answering service, it's an extension of your company. Our professional representatives take pride in being your direct line of communication with existing customers, potential customers and valued business partners. Before we start fielding calls, our representatives are trained according to the details of your business and industry.</p></div>
    <ul class="ticks">
      <li>24 Hour Answering Service</li>
      <li>Virtual Receptionist / Virtual Assistant</li>
      <li>Live Message Relay</li>
      <li>Help Desk Overflow</li>
      <li>Call Screening</li>
      <li>Bilingual Answering (Spanish Answering Service)</li>
      <li>Automated Services</li>
    </ul>
  </div>

  <div class="layer col-auto">
    <span class="label">Automated Services</span>
    <div class="copy">
      <p>Live answering services are not necessary for all businesses. Clearline Response offers automated answering services as a cost-effective option for continuous customer contact. And just because it's "automated" that doesn't mean it isn't tailored to the specific needs of your business.</p>
      <p>(Live and automated services can be combined for a very cost effective and professional solution.)</p>
      <p>Here are some of the customizable automated solutions we offer for businesses of all sizes:</p>
    </div>
    <ul class="ticks">
      <li>Voice Mail (with or without extensions/sub-boxes)</li>
      <li>Voice Mail with Operator Revert</li>
      <li>Call Routing &amp; Transfer</li>
      <li>Web Integration</li>
      <li>Database Interaction</li>
      <li>Text Messaging</li>
      <li>Alpha Paging</li>
      <li>Email</li>
      <li>Fax</li>
      <li>Combination Service – Utilize our reliable voice mail system with an operator revert functionality. Your callers have the option of pressing "0" for a representative at any time.</li>
    </ul>
    <span class="label">Call Center Services Done Right</span>
    <div class="copy"><p>Talbrook is a complete call center provider. We train our representatives to follow your business protocol and then they are able to work as an autonomous unit that only requires your attention if you wish to change a procedure. Our call center representatives handle everything from pre-qualification to appointment setting and order taking. The Clearline Response team is your team.</p></div>
    <div class="subhead">Our call center services include:</div>
    <ul class="ticks">
      <li>Order Taking (on your site or our system)</li>
      <li>Pre-Qualification</li>
      <li>Help Desk</li>
      <li>Appointment Setting</li>
      <li>Appointment Confirmation</li>
      <li>Lead Generation</li>
      <li>Order Processing</li>
    </ul>
  </div>

  <div class="layer col-special">
    <span class="label">Special Services</span>
    <div class="copy"><p>Medical Answering Services – Clearline Response representatives understand the unique needs of the medical community and are trained to provide the support you need.</p></div>
    <ul class="ticks">
      <li>HIPAA compliant messaging system</li>
      <li>Medical messages stored securely for 1 year</li>
      <li>Disaster Recovery – stay in contact with employees, management and customers in the event of emergency</li>
    </ul>
    <div class="copy" style="margin-top:14px">
      <p style="margin-bottom:0">Oil and Gas – We serve many clients in the Energy industry and our representatives are well-versed in handling customer relations in what can be a demanding field.</p>
      <p style="margin-bottom:0">Commercial Property Management – Our representatives have experience maintaining positive relations with tenants, property managers and other real estate personnel.</p>
      <p>*Ask one of our representatives about custom solutions for your industry</p>
    </div>
    <div style="height:12px"></div>
    <span class="label">Test Drive</span>
    <div class="copy"><p>There's no better way to get a feel for our services than by speaking with one of our own representatives – 866.555.CALL.</p></div>
  </div>
</section>

</body>
</html>
```